Business Card For Halvenmoor Financial Consulting

Hi, I would like a business card designed. Bold, modern.
Please use the same design as the logo. I have also attached the website design to see the overall theme.
Wordmark Font
Color: Hex: #01AEF7

```html
<!DOCTYPE html>
<html lang="en">
<head>
<meta charset="utf-8">
<title>Halvenmoor Financial Consulting – Business Card</title>
<link href="https://fonts.googleapis.com/css2?family=Lato:wght@400;700;900&display=swap" rel="stylesheet">
<style>
  :root {
    --stage: #2e2f31;
    --navy: #19232d;
    --navy-deep: #111a22;
    --brand-blue: #01aef7;
    --frame-light: #7fbff0;
    --frame-dark: #2a4763;
    --white: #ffffff;
  }
  html, body {
    margin: 0;
    padding: 0;
    width: 1200px;
    height: 875px;
    overflow: hidden;
    background: var(--stage);
    font-family: "Lato", Arial, sans-serif;
  }
  .canvas {
    position: relative;
    width: 1200px;
    height: 875px;
  }
  .card {
    position: absolute;
    width: 560px;
    height: 320px;
    overflow: hidden;
    box-shadow: 0 18px 40px rgba(0,0,0,0.45);
  }

  /* Front */
  .card--front {
    left: 70px;
    top: 90px;
    background: linear-gradient(135deg, var(--frame-light), var(--frame-dark) 55%, var(--frame-light));
  }
  .card--front .card__inner {
    position: absolute;
    inset: 12px;
    background: var(--navy);
  }
  .card--front .wordmark {
    position: absolute;
    left: 50px;
    top: 118px;
    font-size: 44px;
    letter-spacing: 3px;
  }
  .wordmark {
    margin: 0;
    font-weight: 900;
    color: var(--white);
    line-height: 1.05;
    text-transform: uppercase;
  }

  /* Back */
  .card--back {
    left: 570px;
    top: 465px;
    background: var(--brand-blue);
  }
  .card__curve {
    position: absolute;
    inset: 0;
  }
  .brand {
    position: absolute;
    left: 40px;
    top: 140px;
    display: flex;
    align-items: center;
    gap: 12px;
  }
  .brand__square {
    width: 30px;
    height: 30px;
    border: 3px solid var(--brand-blue);
    box-sizing: border-box;
  }
  .brand .wordmark {
    font-size: 20px;
    letter-spacing: 2px;
  }
  .contact {
    position: absolute;
    right: 26px;
    top: 62px;
    text-align: right;
    color: var(--white);
  }
  .contact__name {
    margin: 0;
    font-size: 22px;
    font-weight: 900;
    letter-spacing: 0.5px;
  }
  .contact__role {
    margin: 2px 0 16px;
    font-size: 14px;
  }
  .contact__list {
    list-style: none;
    margin: 0;
    padding: 0;
    font-size: 12px;
    line-height: 19px;
  }
  .contact__list li {
    display: flex;
    justify-content: flex-end;
    align-items: center;
    gap: 7px;
    white-space: nowrap;
  }
  .icon {
    width: 11px;
    height: 11px;
    fill: var(--white);
    flex: none;
  }
</style>
</head>
<body>
<main class="canvas">

  <section class="card card--front" aria-label="Card front">
    <div class="card__inner">
      <p class="wordmark">Halvenmoor<br>Consulting</p>
    </div>
  </section>

  <section class="card card--back" aria-label="Card back">
    <svg class="card__curve" viewBox="0 0 560 320" preserveAspectRatio="none" aria-hidden="true">
      <path d="M0 0 H306 C342 90 326 230 224 320 H0 Z" fill="#ffffff"/>
      <path d="M0 0 H296 C332 90 314 230 210 320 H0 Z" fill="#19232d"/>
    </svg>

    <div class="brand">
      <span class="brand__square"></span>
      <p class="wordmark">Halvenmoor<br>Consulting</p>
    </div>

    <div class="contact">
      <h1 class="contact__name">DANIEL REYES</h1>
      <p class="contact__role">Founder &amp; CEO</p>
      <ul class="contact__list">
        <li>Your Address, City
          <svg class="icon" viewBox="0 0 12 12"><path d="M6 0a4 4 0 0 0-4 4c0 3 4 8 4 8s4-5 4-8a4 4 0 0 0-4-4zm0 5.6A1.6 1.6 0 1 1 6 2.4a1.6 1.6 0 0 1 0 3.2z"/></svg>
        </li>
        <li>State, Zip 1235<span class="icon"></span></li>
        <li>(555) 014-2231
          <svg class="icon" viewBox="0 0 12 12"><path d="M2.4 0.6 4.2 2.4 3.2 4a7 7 0 0 0 4.8 4.8l1.6-1 1.8 1.8-1.2 1.8C5 11.2 0.8 7 0.6 1.8z"/></svg>
        </li>
        <li>(555) 019-7746
          <svg class="icon" viewBox="0 0 12 12"><path d="M3 0h6v12H3zM4 1.5v8h4v-8z"/></svg>
        </li>
        <li>info@halvenmoorconsulting.com
          <svg class="icon" viewBox="0 0 12 12"><path d="M0 2h12v8H0zM1 3v.4l5 3.2 5-3.2V3z"/></svg>
        </li>
        <li>halvenmoorconsulting.com
          <svg class="icon" viewBox="0 0 12 12"><path d="M6 0a6 6 0 1 0 0 12A6 6 0 0 0 6 0zm0 1.2c.8 0 1.6 2 1.7 4.2H4.3C4.4 3.2 5.2 1.2 6 1.2zM4.3 6.6h3.4C7.6 8.8 6.8 10.8 6 10.8S4.4 8.8 4.3 6.6z"/></svg>
        </li>
      </ul>
    </div>
  </section>

</main>
</body>
</html>
```